MRT Property - Business Cards

Looking for a business card & general letterhead, signage etc design for our new logo.

Colours:
000a20
0056a2
00b5ef
0088ce
68cef2

Fonts:
Poppins
Karla

Please keep look and feel of new brand - example in the zip package I sent.

```html
<!DOCTYPE html>
<html lang="en">
<head>
<meta charset="utf-8">
<title>MRT Property – Business Cards</title>
<link rel="stylesheet" href="https://fonts.googleapis.com/css2?family=Poppins:wght@400;500;600&display=swap">
<style>
  :root {
    --stage: #222222;
    --card: #0e1226;
    --navy: #000a20;
    --blue: #0056a2;
    --mid-blue: #0088ce;
    --cyan: #00b5ef;
    --sky: #68cef2;
    --white: #ffffff;
    --text-light: #e6ecf5;
  }
  * { margin: 0; padding: 0; box-sizing: border-box; }
  html, body {
    width: 1200px; height: 780px; overflow: hidden;
    background: var(--stage);
    font-family: "Poppins", sans-serif;
  }
  .sheet {
    width: 1200px; height: 780px;
    display: flex; align-items: center; justify-content: center; gap: 40px;
  }
  .card {
    position: relative;
    width: 540px; height: 330px;
    background: var(--card);
    overflow: hidden;
  }
  .card__wave { position: absolute; inset: 0; width: 100%; height: 100%; }

  .brand {
    position: absolute;
    font-weight: 600;
    letter-spacing: 0.5px;
    line-height: 1;
  }
  .card--front .brand { left: 36px; top: 34px; font-size: 30px; color: var(--blue); }
  .card--back .brand { right: 40px; bottom: 40px; font-size: 30px; color: var(--white); }

  .contacts {
    position: absolute; left: 36px; top: 92px;
    list-style: none;
    font-size: 11px; color: var(--text-light);
  }
  .contacts li { display: flex; align-items: center; gap: 8px; margin-bottom: 5px; }
  .contacts svg { width: 11px; height: 11px; fill: var(--mid-blue); flex: none; }

  .person { position: absolute; right: 44px; top: 120px; text-align: right; }
  .person__name { font-size: 28px; font-weight: 500; color: var(--blue); line-height: 1.1; }
  .person__name span { color: var(--sky); }
  .person__role { font-size: 13px; color: var(--white); }
  .tab {
    position: absolute; right: 0; top: 150px;
    width: 18px; height: 34px; background: var(--sky);
  }

  .address {
    position: absolute; right: 44px; bottom: 36px;
    font-size: 12.5px; color: var(--text-light); text-align: right; line-height: 1.45;
    font-style: normal;
  }
</style>
</head>
<body>
<main class="sheet">

  <section class="card card--front">
    <svg class="card__wave" viewBox="0 0 540 330" preserveAspectRatio="none" aria-hidden="true">
      <path d="M0 250 C120 268 230 296 300 330 L0 330 Z" fill="var(--sky)"/>
      <path d="M0 268 C110 282 205 304 262 330 L0 330 Z" fill="var(--card)"/>
      <path d="M0 276 C100 290 180 308 225 330 L0 330 Z" fill="var(--blue)"/>
    </svg>

    <div class="brand">MRT Property</div>

    <ul class="contacts">
      <li>
        <svg viewBox="0 0 24 24"><path d="M6.6 10.8a15 15 0 0 0 6.6 6.6l2.2-2.2a1 1 0 0 1 1-.25 11.4 11.4 0 0 0 3.6.57 1 1 0 0 1 1 1V20a1 1 0 0 1-1 1A17 17 0 0 1 3 4a1 1 0 0 1 1-1h3.5a1 1 0 0 1 1 1c0 1.25.2 2.45.57 3.57a1 1 0 0 1-.25 1z"/></svg>
        +61 2 9000 1234
      </li>
      <li>
        <svg viewBox="0 0 24 24"><path d="M12 2a10 10 0 1 0 0 20 10 10 0 0 0 0-20zm6.9 6h-3a15.7 15.7 0 0 0-1.4-3.6A8 8 0 0 1 18.9 8zM12 4c.8 1.2 1.5 2.5 1.9 4h-3.8c.4-1.5 1.1-2.8 1.9-4zM4.3 14a8 8 0 0 1 0-4h3.4a16 16 0 0 0 0 4zm.8 2h3a15.7 15.7 0 0 0 1.4 3.6A8 8 0 0 1 5.1 16zm3-8h-3a8 8 0 0 1 4.4-3.6A15.7 15.7 0 0 0 8.1 8zM12 20c-.8-1.2-1.5-2.5-1.9-4h3.8c-.4 1.5-1.1 2.8-1.9 4zm2.3-6H9.7a14.6 14.6 0 0 1 0-4h4.6a14.6 14.6 0 0 1 0 4zm.2 5.6a15.7 15.7 0 0 0 1.4-3.6h3a8 8 0 0 1-4.4 3.6zm1.8-5.6a16 16 0 0 0 0-4h3.4a8 8 0 0 1 0 4z"/></svg>
        www.mrtproperty.com.au
      </li>
      <li>
        <svg viewBox="0 0 24 24"><path d="M20 4H4a2 2 0 0 0-2 2v12a2 2 0 0 0 2 2h16a2 2 0 0 0 2-2V6a2 2 0 0 0-2-2zm0 4-8 5-8-5V6l8 5 8-5z"/></svg>
        info@mrtproperty.com.au
      </li>
    </ul>

    <div class="person">
      <p class="person__name">Callum <span>Reyes</span></p>
      <p class="person__role">Director</p>
    </div>
    <div class="tab"></div>

    <address class="address">
      Suite 4.12, Tower 3<br>
      18 Harbourline Road<br>
      Riverton Park NSW 2199
    </address>
  </section>

  <section class="card card--back">
    <div class="brand">MRT Property</div>
  </section>

</main>
</body>
</html>
```